Business Card Design Project

I need a business card designed from scratch. I have an existing logo that I can upload in Illustrator for modification or redesign.

The Company is called Query Lanterns http://querylanterns.com.au and we provide Search Engine Optimization services to Australian businesses. The current logo signifies an increase in visitors, profits etc...

There are no restrictions as to the redesign - colours, style etc are all open to change.

Cards will be full colour and one sided printed at http://www.cardmoxel.com.au so check their requirements for file format and sizes etc.

I will expect all original files upon completion of project.

Target Market(s)

Any business with a web site looking to improve their search engine rankings

Industry/Entity Type

Business

Requirements
Must have
• I like modern, sleek designs. Clean, not fussy, uncluttered.

```html
<!DOCTYPE html>
<html lang="en">
<head>
<meta charset="utf-8">
<title>Query Lanterns – Business Card</title>
<link rel="stylesheet" href="https://fonts.googleapis.com/css2?family=Source+Sans+3:wght@400;600;700&display=swap">
<style>
  :root {
    --backdrop: #b8892c;
    --card: #232323;
    --card-glow: #2e2e2e;
    --brand-blue: #1b78c2;
    --accent-yellow: #f2bb1c;
    --text-light: #f1f1f1;
    --divider: rgba(255, 255, 255, 0.55);
  }
  * { margin: 0; padding: 0; box-sizing: border-box; }
  html, body {
    width: 1200px;
    height: 686px;
    overflow: hidden;
    background: var(--backdrop);
    font-family: "Source Sans 3", "Myriad Pro", sans-serif;
  }
  .canvas {
    position: relative;
    width: 1200px;
    height: 686px;
    background: var(--backdrop);
  }
  .card {
    position: absolute;
    width: 483px;
    height: 275px;
    border-radius: 26px;
    background: radial-gradient(ellipse at 50% 40%, var(--card-glow) 0%, var(--card) 70%);
    color: var(--text-light);
    text-align: center;
  }
  .card--front { left: 95px; top: 155px; }
  .card--back  { left: 612px; top: 286px; }

  .brand {
    position: absolute;
    left: 0;
    right: 0;
    display: flex;
    align-items: center;
    justify-content: center;
    gap: 10px;
  }
  .card--front .brand { top: 58px; }
  .card--back .brand  { top: 124px; }
  .brand__dot {
    width: 16px;
    height: 16px;
    border-radius: 50%;
    background: var(--accent-yellow);
  }
  .brand__name {
    font-weight: 700;
    font-size: 34px;
    line-height: 1;
    color: var(--brand-blue);
    letter-spacing: -0.3px;
  }

  .divider {
    position: absolute;
    left: 138px;
    top: 147px;
    width: 207px;
    height: 1px;
    background: linear-gradient(90deg, transparent, var(--divider), transparent);
  }

  .details {
    position: absolute;
    left: 0;
    right: 0;
    top: 166px;
  }
  .details__name-line {
    font-size: 17px;
    line-height: 22px;
  }
  .person-name { color: var(--brand-blue); font-weight: 600; }
  .sep { color: var(--brand-blue); margin: 0 5px; font-size: 14px; }
  .person-title { color: var(--accent-yellow); font-weight: 600; font-size: 13px; }
  .details__line {
    font-size: 13px;
    line-height: 20px;
    color: var(--text-light);
  }
  .contact-item {
    display: inline-flex;
    align-items: center;
    gap: 3px;
    margin: 0 5px;
  }
  .contact-item svg { display: block; }
  .website { font-weight: 600; color: var(--brand-blue); }
  .website__domain { color: var(--accent-yellow); }
</style>
</head>
<body>
<main class="canvas">

  <section class="card card--front" aria-label="Card front">
    <div class="brand">
      <span class="brand__dot"></span>
      <span class="brand__name">Query Lanterns</span>
    </div>
    <div class="divider"></div>
    <div class="details">
      <p class="details__name-line">
        <span class="person-name">Your Name</span><span class="sep">|</span><span class="person-title">Title</span>
      </p>
      <p class="details__line">Street name City, State, zip code</p>
      <p class="details__line">
        <span class="contact-item">
          <svg width="10" height="11" viewBox="0 0 10 11" aria-hidden="true"><path d="M2 0.5 L4 3 L3 4.5 Q4 7 6 8 L7.5 7 L9.5 9 L8 10.5 Q3 10 0.5 3 Z" fill="#1b78c2"/></svg>
          123-456-7890
        </span>
        <span class="contact-item">
          <svg width="12" height="9" viewBox="0 0 12 9" aria-hidden="true"><rect x="0" y="0" width="12" height="9" rx="1" fill="#1b78c2"/><path d="M0.5 0.8 L6 5 L11.5 0.8" stroke="#232323" stroke-width="1.2" fill="none"/></svg>
          inquiry@querylanterns.com.au
        </span>
      </p>
      <p class="details__line website">www.<span class="website__domain">querylanterns</span>.com.au</p>
    </div>
  </section>

  <section class="card card--back" aria-label="Card back">
    <div class="brand">
      <span class="brand__dot"></span>
      <span class="brand__name">Query Lanterns</span>
    </div>
  </section>

</main>
</body>
</html>
```